Web Design Project

Looking for an eye catching banner page to be used on the website and LinkedIn. We are an Executive Recruiting and HR Consulting service firm with a modern edge. We want to demonstrate through our brand that we are using the latest recruiting trends to find talent and that we are easy to work with- innovative and simple.We typically recruit for Engineers, IT professionals, Accounting and Operation Managers. Our website is www.bluvantatalent.com and it needs a fresh clean look. We love our logo but might want to use the "8" to show the 2 sides of our business or maybe to use the infinity concept or continuous improvement. We like the Green and white colors with accents in gray.

Target Market(s)

Small to mid-sized Business Managers seeking innovation

Industry/Entity Type

Business

Requirements
Must have
• Use of the 8
Long picture on top to be used on LinkedIn and the website top
Clean Simple look- modern font like century gothic
Nice to have
• Smiling face(s)
Layered image of 8 or of photo stock faces
Maybe a modern office so they feel that they walked in to meet us (fyi our office has white chandeliers and green walls that match our logo)
Should not have
• Busy or cluttered feel

```html
<!DOCTYPE html>
<html lang="en">
<head>
<meta charset="utf-8">
<title>Bluvanta – Where Strategy Meets Recruiting</title>
<link href="https://fonts.googleapis.com/css2?family=Questrial&family=Arimo:wght@400;700&display=swap" rel="stylesheet">
<style>
:root{
  --green:#9dbb38;
  --green-dark:#86a427;
  --green-foot:#a5bf46;
  --green-pale:#eef2e2;
  --grey:#6c757a;
  --grey-nav:#9ba4a9;
  --grey-dark:#4f575c;
  --grey-line:#d6d9da;
  --text:#333;
  --white:#fff;
}
*{box-sizing:border-box;margin:0;padding:0}
html,body{width:1000px;height:1200px;overflow:hidden}
body{position:relative;background:var(--white);font-family:"Arimo",Arial,sans-serif;color:var(--text)}
.abs{position:absolute}
.top-strip{left:0;top:0;width:1000px;height:6px;background:var(--green)}
.brand{left:186px;top:36px}
.brand-name{display:flex;align-items:center;gap:10px;font-family:"Questrial",sans-serif;font-size:50px;color:var(--green);letter-spacing:2px;line-height:1}
.brand-dot{width:30px;height:30px;border-radius:50%;background:var(--grey);display:inline-block}
.brand-tag{font-family:"Questrial",sans-serif;font-size:8.5px;letter-spacing:2.4px;color:var(--grey-dark);margin-top:10px}
.util-links{right:192px;top:22px;font-size:9px;font-weight:700;display:flex;gap:14px}
.util-links span{display:flex;align-items:center;gap:4px}
.util-links i{width:8px;height:8px;background:var(--grey);display:inline-block}
.btn-big{top:56px;width:94px;height:26px;background:linear-gradient(#b2cd4f,var(--green-dark));color:var(--white);font-size:12px;text-align:center;line-height:26px;border-radius:2px;border:1px solid #7f9b25}
.search{left:686px;top:93px;width:126px;height:19px;border:1px solid var(--grey-line);font-size:10px;font-style:italic;font-weight:700;color:var(--green);padding:3px 7px;border-radius:2px}
.search svg{position:absolute;right:5px;top:3px}
.nav{left:186px;top:120px;width:626px;height:32px;background:linear-gradient(#a6aeb3,#8d969b);border:1px solid #848d92;display:flex;align-items:center;padding-left:46px;gap:12px;font-size:8.8px;color:var(--white);white-space:nowrap;overflow:hidden}
.nav .active{border-bottom:2px solid var(--white);padding-bottom:2px}
.hero{left:186px;top:160px;width:626px;height:217px;background:linear-gradient(90deg,#e8ebe0 0%,#dfe6c9 35%,#c3d67a 48%,#cfd3d4 60%,#8e9397 100%)}
.hero-caption{left:186px;top:340px;width:526px;height:37px;background:rgba(157,187,56,.9);color:var(--white);font-family:"Questrial",sans-serif;font-size:13px;line-height:15px;padding:3px 12px}
.hero-arrow{top:255px;width:20px;height:20px;border-radius:50%;background:var(--white);border:2px solid var(--green)}
.hero-arrow svg{position:absolute;left:4px;top:4px}
.intro-rule{left:186px;top:416px;width:626px;height:2px;background:var(--green)}
.intro-ring{left:202px;top:390px;width:54px;height:54px;border-radius:50%;border:4px solid var(--green);background:var(--white)}
.intro-title{right:188px;top:386px;font-family:"Questrial",sans-serif;font-size:22px;color:var(--grey-dark)}
.intro-copy{left:186px;top:454px;width:626px;font-size:9px;line-height:11.5px}
.intro-copy p{margin-bottom:10px}
.btn-small{height:16px;background:linear-gradient(#b2cd4f,var(--green-dark));color:var(--white);font-size:8px;font-weight:700;text-align:center;line-height:16px;border-radius:2px}
.services{left:0;top:544px;width:1000px;height:122px;background:linear-gradient(#e6e7e8,#fafafa 15%,#f2f3f3 85%,#dcdedf);border-top:1px solid var(--grey-line);border-bottom:1px solid var(--grey-line)}
.service{top:560px;width:200px;text-align:center;font-family:"Questrial",sans-serif;font-weight:700;font-size:11.5px;color:#2c3235;white-space:nowrap}
.service .disc{width:74px;height:74px;border-radius:50%;background:var(--grey);border:4px solid #9aa2a6;margin:0 auto 12px;position:relative}
.service .disc::after{content:"";position:absolute;left:18px;top:18px;width:30px;height:30px;border-radius:50%;background:#4f575c}
.service.on .disc{background:var(--green);border-color:#cfe07f}
.service.on .disc::after{background:#3f4a1a}
.numbers{left:186px;top:684px;width:414px;height:200px;border:1px solid var(--grey-line);background:var(--white)}
.numbers-head{height:36px;background:var(--green);color:var(--white);font-family:"Questrial",sans-serif;font-size:17px;padding:7px 10px}
.numbers-list{margin:6px;background:var(--green-pale);height:148px;padding:8px 12px 0 10px;list-style:none;font-size:8.4px;line-height:12.5px;position:relative}
.numbers-list li{position:relative;padding-left:14px;margin-bottom:12px;padding-right:4px}
.numbers-list li::before{content:"";position:absolute;left:0;top:2px;width:9px;height:9px;border-radius:50%;background:var(--green)}
.scrollbar{right:4px;top:4px;width:6px;height:140px;border:1px solid #c8ccc0;background:var(--white)}
.scrollbar::after{content:"";position:absolute;left:0;top:0;width:4px;height:56px;background:#c9ccc4}
.testimonial{left:618px;top:684px;width:194px;height:200px;border:1px solid var(--grey-line);background:#f9f9f9;padding:8px 17px}
.testimonial h3{font-family:"Questrial",sans-serif;font-weight:400;font-size:17px;color:#2c3235;margin-bottom:8px}
.testimonial p{font-size:9px;line-height:14.6px;text-align:justify}
.testimonial .who{text-align:right;font-weight:700;font-size:8.5px;margin-top:18px}
.footer{left:0;top:936px;width:1000px;height:232px;background:radial-gradient(ellipse at 50% 100%,#c7d872 0%,var(--green-foot) 55%,#96b13a 100%);border-top:1px solid #8ea636}
.social-tab{left:408px;top:910px;width:186px;height:30px;background:#f4f5f5;border:1px solid var(--grey-line);border-bottom:none;border-radius:14px 14px 0 0;display:flex;gap:5px;justify-content:center;padding-top:8px}
.social-tab i{width:19px;height:19px;border-radius:3px;background:var(--grey);display:block}
.foot-col{top:972px;font-size:8.6px;color:var(--white)}
.foot-col h4{font-family:"Questrial",sans-serif;font-weight:400;font-size:12.5px;padding-bottom:6px;border-bottom:1px solid rgba(255,255,255,.6);margin-bottom:10px;width:95px}
.foot-col li{list-style:none;line-height:16.8px}
.contact-row{display:flex;gap:10px;align-items:center;margin-top:8px}
.contact-row .ico{width:14px;display:flex;justify-content:center}
.big-phone{font-size:13px}
.badge{left:188px;top:1104px;width:106px;height:50px;border:3px solid var(--white);border-radius:6px;background:#e6ecef}
.jobs{left:469px;top:974px;width:157px;height:180px;background:var(--white);border:1px solid var(--grey-line)}
.jobs h4{height:25px;background:#7f9b25;color:var(--white);font-family:"Questrial",sans-serif;font-weight:400;font-size:12.5px;text-align:center;line-height:25px}
.jobs ul{list-style:none;padding:10px 8px;font-size:8.8px;line-height:11px}
.jobs li{margin-bottom:7px}
.fans{left:643px;top:974px;width:160px;height:180px;background:var(--white);border:1px solid var(--grey-line);font-size:7px}
.fans-head{padding:10px 8px;display:flex;align-items:center;gap:8px;font-size:11px;color:#3b5f9a;border-bottom:1px solid #eee}
.fans-head span.like{font-size:7.5px;border:1px solid #ccc;padding:1px 4px;color:#333}
.fans-count{padding:10px 8px 5px}
.fans-grid{display:grid;grid-template-columns:repeat(4,32px);gap:4px;padding:0 8px}
.fans-grid div{height:32px;background:linear-gradient(#b9bcc0,#8a8f94)}
.fans-foot{position:absolute;left:0;bottom:0;width:100%;padding:4px 6px;border-top:1px solid #ddd;color:#555}
.bottom-bar{left:0;top:1168px;width:1000px;height:32px;background:#5b6367;color:var(--white);font-size:8px;text-align:center;line-height:32px}
</style>
</head>
<body>
<div class="abs top-strip"></div>

<div class="abs brand">
  <div class="brand-name"><span>BLUVANTA</span><span class="brand-dot"></span></div>
  <div class="brand-tag">WHERE STRATEGY MEETS RECRUITING</div>
</div>

<div class="abs util-links"><span><i></i>Home</span><span><i></i>Contact</span></div>
<div class="abs btn-big" style="left:619px">Candidate</div>
<div class="abs btn-big" style="left:718px">Clients</div>
<div class="abs search">Search
  <svg width="11" height="11" viewBox="0 0 11 11"><circle cx="4.5" cy="4.5" r="3.3" fill="none" stroke="#9dbb38" stroke-width="1.6"/><line x1="7" y1="7" x2="10" y2="10" stroke="#9dbb38" stroke-width="1.8"/></svg>
</div>

<nav class="abs nav">
  <span class="active">Recruiting Services</span><span>HR consulting Services</span><span>Testimonials</span><span>Job Openings</span><span>Job Search Assistance</span><span>Job Application</span><span>Blog</span>
</nav>

<div class="abs hero" role="img" aria-label="Photo of a bright modern office with green walls and a smiling team of recruiting professionals"></div>
<div class="abs hero-caption">Bluvanta demonstrated extraordinary insight in understanding both the client recruiting needs and the candidates' objectives"</div>
<div class="abs hero-arrow" style="left:180px"><svg width="8" height="8" viewBox="0 0 8 8"><path d="M6 0L1 4l5 4z" fill="#9dbb38"/></svg></div>
<div class="abs hero-arrow" style="left:796px"><svg width="8" height="8" viewBox="0 0 8 8"><path d="M2 0l5 4-5 4z" fill="#9dbb38"/></svg></div>

<div class="abs intro-rule"></div>
<div class="abs intro-ring"></div>
<h2 class="abs intro-title" style="font-weight:400">Where strategy meets recruiting</h2>
<div class="abs intro-copy">
  <p>The modern and successful recruiting leader begins with a strategic foundation, leverages connectivity through social media, stakeholder relationships and builds pipelines of competencies, quickly and flexibly to solve pressing employment challenges.</p>
  <p>Bluvanta combines strategy and action to find top talent in the areas of Engineering, IT, Operations, and Accounting and Administration. Look to Bluvanta to explore new pathways to strategic relevancy. From strategy to execution, we are the team you need… NOW!</p>
  <p>How can we be your strategic partner to success?</p>
</div>
<div class="abs btn-small" style="left:744px;top:514px;width:60px">Learn more</div>

<div class="abs services"></div>
<div class="abs service" style="left:182px"><div class="disc"></div>Expert Recruiting</div>
<div class="abs service" style="left:398px"><div class="disc"></div>Recruiting Strategy</div>
<div class="abs service on" style="left:614px"><div class="disc"></div>Human Resource Consulting</div>

<section class="abs numbers">
  <div class="numbers-head">Here at Bluvanta, we love our numbers!</div>
  <ul class="numbers-list">
    <li>8 is known as the beginning and long symbolized for good luck, to us it means that and more!</li>
    <li>76% of all employees are passively searching for a new position, we must find ways to keep your talent engaged as well as identy the right new talent for your organization</li>
    <li>52% of companies are expecting to grow in the next 6 months</li>
    <li>$8,947 is the national average cost per hire—up approximately 57% from $5,708 in 2009, we can show you how to reduce the cost and increase quality</li>
    <div class="abs scrollbar"></div>
  </ul>
</section>

<section class="abs testimonial">
  <h3>Testimonials</h3>
  <p>Bluvanta has been very attentive to the needs of our Corporation. From providing administrative to technical candidates, they operate in a professional manor and will go above and beyond to achieve exceptional results</p>
  <div class="who">Orbital Contract Company</div>
</section>
<div class="abs btn-small" style="left:720px;top:860px;width:84px">More Testimonials</div>

<div class="abs footer"></div>
<div class="abs social-tab"><i></i><i></i><i></i><i></i><i></i><i></i></div>

<div class="abs foot-col" style="left:191px">
  <h4>About Bluvanta</h4>
  <ul><li>About Us</li><li>What we do</li><li>How we do</li><li>Testimonials</li><li>Our awards</li><li>Our Partners</li></ul>
</div>
<div class="abs badge" role="img" aria-label="Certification badge"></div>

<div class="abs foot-col" style="left:317px">
  <h4 style="width:100px">Contact Us</h4>
  <ul><li>Contact Bluvanta</li><li>Help &amp; Links</li></ul>
  <div class="contact-row"><span class="ico"><svg width="10" height="14" viewBox="0 0 10 14"><path d="M5 0a5 5 0 0 1 5 5c0 4-5 9-5 9S0 9 0 5a5 5 0 0 1 5-5z" fill="#fff"/><circle cx="5" cy="5" r="2" fill="#a5bf46"/></svg></span><span style="line-height:11px">2280 Meridian Park Dr<br>Houston, TX, 77001</span></div>
  <div class="contact-row"><span class="ico"><svg width="14" height="10" viewBox="0 0 14 10"><rect x=".5" y=".5" width="13" height="9" fill="none" stroke="#fff"/><path d="M.5.5l6.5 5 6.5-5" fill="none" stroke="#fff"/></svg></span><span>info@bluvantatalent.com</span></div>
  <div class="contact-row"><span class="ico"><svg width="13" height="13" viewBox="0 0 13 13"><path d="M2 0l3 3-1.5 2a7 7 0 0 0 4.5 4.5L10 8l3 3-2 2C5 13 0 8 0 2z" fill="#fff"/></svg></span><span class="big-phone">281.555.0142</span></div>
  <div class="contact-row"><span class="ico"><svg width="14" height="12" viewBox="0 0 14 12"><rect x="3" y="0" width="8" height="4" fill="#fff"/><rect x="0" y="4" width="14" height="6" fill="#fff"/><rect x="3" y="8" width="8" height="4" fill="#fff" stroke="#a5bf46"/></svg></span><span class="big-phone">713.555.0187</span></div>
</div>

<section class="abs jobs">
  <h4>Job Openings</h4>
  <ul>
    <li>- Houstan is hiring</li>
    <li>- Corvane is looking for a decent Art director</li>
    <li>- Nexiom is hiring developer</li>
    <li>- Corvane is looking for a decent designer</li>
  </ul>
</section>
<div class="abs btn-small" style="left:508px;top:1130px;width:86px">More Vacancies</div>

<section class="abs fans">
  <div class="fans-head"><span style="font-weight:700">Bluvanta</span><span class="like">Like</span></div>
  <div class="fans-count">8,046 people like <b style="color:#3b5f9a">Bluvanta</b></div>
  <div class="fans-grid" role="img" aria-label="Grid of follower profile photos">
    <div></div><div></div><div></div><div></div><div></div><div></div><div></div><div></div>
  </div>
  <div class="fans-foot">Circlepage social plugin</div>
</section>

<div class="abs bottom-bar">Copyright © 2013 Bluvanta All rights reserved. &nbsp;/&nbsp; Site Map &nbsp;/&nbsp; Disclaimers</div>
</body>
</html>
```